Small Business Broker Business Card Design

A business card design for a small business brokerage, which is a financial service, not unlike real estate brokerage, but for small businesses such as laundromats, pizza shops, restaurants, cleaners etc. The designs should all be simple, more conservative in nature, using the colors and font of the logo. Again, think real estate Brokerage as a business context
Contact Information for Business Card
Name: Glen R. Harlow. Title: Small Business Advisor. Email: g.harlow@bayfieldcapitalworks.example. Mobile: (555) 274-3918. Office: (555) 806-2147. www.bayfieldcapitalworks.example

```html
<!DOCTYPE html>
<html lang="en">
<head>
<meta charset="utf-8">
<title>Bayfield Capital Works – Business Card</title>
<link href="https://fonts.googleapis.com/css2?family=Montserrat:wght@400;500;700;800&display=swap" rel="stylesheet">
<style>
  :root{
    --navy:#1c3a6e;
    --green:#8cc63f;
    --green-light:#a6d65c;
    --ink:#1d1d1f;
    --paper:#ffffff;
    --stage:#e9ebee;
  }
  *{box-sizing:border-box;margin:0;padding:0}
  html,body{width:1200px;height:800px;overflow:hidden}
  body{
    background:var(--stage);
    font-family:"Montserrat",sans-serif;
    position:relative;
  }
  .card{
    position:absolute;
    top:240px;
    width:560px;height:320px;
    border-radius:18px;
    overflow:hidden;
    box-shadow:0 8px 24px rgba(0,0,0,.18);
  }

  /* Back side */
  .card-back{left:30px;background:var(--green)}
  .card-back .texture{
    position:absolute;inset:0;
    background:linear-gradient(200deg,var(--green-light) 0%,var(--green) 55%,#84bd3a 100%);
  }
  .card-back .brand{
    position:absolute;left:0;right:0;top:128px;
    text-align:center;
  }
  .brand-name{
    display:inline-flex;align-items:center;gap:10px;
    font-weight:800;font-size:22px;letter-spacing:.02em;
    color:var(--navy);text-transform:uppercase;
  }
  .brand-mark{width:14px;height:14px;background:var(--navy);flex:none}
  .card-back .tagline{
    margin-top:8px;
    font-weight:700;font-size:11px;letter-spacing:.14em;
    color:var(--paper);text-transform:uppercase;
  }

  /* Front side */
  .card-front{left:610px;background:var(--paper)}
  .card-front .brand{
    position:absolute;left:26px;top:150px;width:240px;
  }
  .card-front .brand-name{font-size:14px;gap:8px;line-height:1.2}
  .card-front .brand-mark{width:12px;height:12px;background:var(--green)}
  .card-front .tagline{
    margin-top:6px;
    font-weight:700;font-size:7.4px;letter-spacing:.1em;
    color:var(--green);text-transform:uppercase;
  }
  .divider{
    position:absolute;left:280px;top:70px;width:1px;height:160px;
    background:var(--navy);
  }
  .contact{
    position:absolute;left:294px;top:74px;right:12px;
  }
  .person-name{
    font-weight:800;font-size:22px;color:var(--navy);line-height:1.1;
  }
  .person-name .surname{color:var(--green)}
  .person-title{
    font-weight:500;font-size:11px;color:var(--ink);margin-top:3px;
  }
  .contact-list{list-style:none;margin-top:18px}
  .contact-list li{
    display:flex;align-items:center;gap:7px;
    font-size:10px;font-weight:400;color:var(--ink);
    line-height:1;margin-bottom:9px;white-space:nowrap;
  }
  .contact-list svg{width:11px;height:11px;flex:none;fill:var(--navy)}
  .edge-bands{position:absolute;left:0;bottom:0;width:560px;height:40px}
</style>
</head>
<body>

<section class="card card-back" aria-label="Card back">
  <div class="texture" role="img" aria-label="Tonal green background pattern"></div>
  <div class="brand">
    <div class="brand-name"><span class="brand-mark"></span>Bayfield Capital Works, Inc</div>
    <div class="tagline">Confidently buy or sell a local business today</div>
  </div>
</section>

<section class="card card-front" aria-label="Card front">
  <div class="brand">
    <div class="brand-name"><span class="brand-mark"></span>Bayfield Capital Works, Inc</div>
    <div class="tagline">Confidently buy or sell a local business today</div>
  </div>

  <div class="divider"></div>

  <div class="contact">
    <h1 class="person-name">Glen R. <span class="surname">Harlow</span></h1>
    <p class="person-title">Small Business Advisor</p>
    <ul class="contact-list">
      <li>
        <svg viewBox="0 0 24 24" aria-hidden="true"><path d="M3 9c0-3 4-5 9-5s9 2 9 5v2h-5V9H8v2H3zM6 12h12l2 8H4z"/></svg>
        (555) 806-2147
      </li>
      <li>
        <svg viewBox="0 0 24 24" aria-hidden="true"><path d="M6.6 10.8a15 15 0 0 0 6.6 6.6l2.2-2.2a1 1 0 0 1 1-.25 11.4 11.4 0 0 0 3.6.57 1 1 0 0 1 1 1V20a1 1 0 0 1-1 1A17 17 0 0 1 3 4a1 1 0 0 1 1-1h3.5a1 1 0 0 1 1 1c0 1.25.2 2.45.57 3.57a1 1 0 0 1-.25 1z"/></svg>
        (555) 274-3918
      </li>
      <li>
        <svg viewBox="0 0 24 24" aria-hidden="true"><path d="M2 5h20v14H2zm2 2v.5l8 5 8-5V7z"/></svg>
        g.harlow@bayfieldcapitalworks.example
      </li>
      <li>
        <svg viewBox="0 0 24 24" aria-hidden="true"><circle cx="12" cy="12" r="10"/><path d="M2 12h20M12 2c3 3 3 17 0 20M12 2c-3 3-3 17 0 20" stroke="#fff" stroke-width="1.5" fill="none"/></svg>
        www.bayfieldcapitalworks.example
      </li>
    </ul>
  </div>

  <svg class="edge-bands" viewBox="0 0 560 40" aria-hidden="true">
    <polygon points="0,30 392,30 384,40 0,40" fill="var(--navy)"/>
    <polygon points="402,18 560,18 560,40 392,40" fill="var(--green)"/>
  </svg>
</section>

</body>
</html>
```